Design a web site for my business - Brightline Coatings Co.

We are a family business that handles design, fabrication and installation of powder coated aluminum, stainless steel and glass products. Including handrails, privacy slat screens, electric gates and pool fencing. We are based in the Whitsundays in North Queensland and service an area from Airlie Beach to Townsville.

Target Market(s)

Domestic and commercial

Industry/Entity Type

fabrication - manufacturing

Coding

Coded - Design and coding required

Number of Pages Required

5+ page

Colors
0054AA
0677BA
7BADD7
CADEEF
E8F1F8

Requirements
Must have
• photo galleries, contact page, one page for privacy screens, balustrades, glass fencing, stainless steel handrail, powder coated aluminium handrails and pool fencing

```html
<!DOCTYPE html>
<html lang="en">
<head>
<meta charset="utf-8">
<title>Contact Us – Brightline Coatings Co</title>
<link href="https://fonts.googleapis.com/css2?family=Outfit:wght@300;400;500;600;700&display=swap" rel="stylesheet">
<style>
:root{
  --page:#f4f7fc;
  --ink:#111418;
  --text:#2f3338;
  --muted:#5f656d;
  --blue:#0054aa;
  --card:#e8f1f8;
  --card-line:#cadeef;
  --icon-bg:#d9e7f4;
  --field-line:#d7dce4;
  --required:#e0242b;
  --footer:#01244f;
  --footer-text:#b9c6d9;
  --footer-copy:#94a6c0;
}
*{box-sizing:border-box;margin:0;padding:0}
html,body{width:807px;height:1200px;overflow:hidden}
body{background:var(--page);font-family:"Outfit",sans-serif;color:var(--text);position:relative}
.abs{position:absolute}

.brand{left:45px;top:20px;display:flex;align-items:center;gap:6px;font-size:11px;font-weight:600;color:#6b6f74;line-height:1}
.brand-mark{width:10px;height:10px;background:#6b6f74}
.nav{top:21px;font-size:10px;color:#555a60;line-height:14px}
.nav.active{color:#2d3034;font-weight:600}
.nav-underline{left:710px;top:53px;width:56px;height:2px;background:#4a4d52}

.eyebrow-line{left:355px;top:140px;width:34px;height:1px;background:var(--blue)}
.eyebrow{left:398px;top:134px;font-size:10.5px;font-weight:500;color:var(--blue);line-height:14px}
.title{left:0;width:807px;top:156px;text-align:center;font-size:26px;font-weight:700;line-height:31px;color:var(--ink);text-transform:uppercase;letter-spacing:-0.3px}
.lead{left:0;width:807px;top:231px;text-align:center;font-size:13px;line-height:17px;color:var(--text)}

.info-card{top:310px;height:56px;background:var(--card);border:1px solid var(--card-line);border-radius:14px}
.info-icon{position:absolute;left:12px;top:12px;width:31px;height:31px;border-radius:8px;background:var(--icon-bg);display:flex;align-items:center;justify-content:center}
.info-title{position:absolute;left:52px;top:14px;font-size:10px;font-weight:600;color:var(--ink);line-height:13px}
.info-value{position:absolute;left:52px;top:29px;font-size:9px;color:#2c3035;line-height:12px;white-space:nowrap}

.label{font-size:12px;line-height:15px;color:var(--ink)}
.label i{font-style:normal;color:var(--required)}
.field{height:37px;border:1px solid var(--field-line);border-radius:8px;background:var(--page);font-size:12px;color:var(--muted);padding-left:15px;display:flex;align-items:center}
.field svg{position:absolute;right:14px;top:14px}
.field.area{height:111px;align-items:flex-start;padding-top:16px;border-radius:10px}

.cta{left:591px;top:822px;width:171px;height:37px;border-radius:19px;background:var(--blue);color:#fff;font-size:13px;font-weight:600;display:flex;align-items:center;justify-content:center;box-shadow:0 3px 8px rgba(0,84,170,.25)}

.footer{left:18px;top:938px;width:771px;height:244px;background:var(--footer);border-radius:21px}
.footer-brand{position:absolute;left:45px;top:38px;display:flex;align-items:center;gap:6px;font-size:11px;font-weight:600;color:#fff;line-height:1}
.footer-brand span.mark{width:10px;height:10px;background:#fff}
.footer-about{position:absolute;left:45px;top:101px;width:180px;font-size:12px;font-weight:300;line-height:18px;color:var(--footer-text)}
.footer-col{position:absolute;top:34px}
.footer-col h3{font-size:12.5px;font-weight:600;color:#fff;line-height:16px;margin-bottom:14px}
.footer-col li{list-style:none;font-size:11px;font-weight:300;color:var(--footer-text);line-height:19px;white-space:nowrap}
.copyright{position:absolute;left:0;width:771px;top:215px;text-align:center;font-size:10.5px;font-weight:300;color:var(--footer-copy);line-height:14px}
</style>
</head>
<body>

<header>
  <div class="abs brand"><span class="brand-mark"></span>Brightline Coatings Co</div>
  <nav>
    <span class="abs nav" style="left:452px">Home</span>
    <span class="abs nav" style="left:505px">About Us</span>
    <span class="abs nav" style="left:572px">Our Services</span>
    <span class="abs nav" style="left:654px">Gallery</span>
    <span class="abs nav active" style="left:712px">Contact Us</span>
    <span class="abs nav-underline"></span>
  </nav>
</header>

<main>
  <span class="abs eyebrow-line"></span>
  <span class="abs eyebrow">Contact Us</span>
  <h1 class="abs title">Let's bring your<br>vision to life</h1>
  <p class="abs lead">Get in touch with our experienced team to discuss<br>your next fabrication project.</p>

  <div class="abs info-card" style="left:45px;width:156px">
    <div class="info-icon"><svg width="15" height="15" viewBox="0 0 24 24" fill="none" stroke="#0054aa" stroke-width="1.8" stroke-linecap="round" stroke-linejoin="round"><path d="M5 3h3l2 5-2.5 1.5a11 11 0 0 0 7 7L16 14l5 2v3a2 2 0 0 1-2 2A17 17 0 0 1 3 5a2 2 0 0 1 2-2z"/></svg></div>
    <div class="info-title">Phone</div>
    <div class="info-value">+1 234 - 567 890</div>
  </div>
  <div class="abs info-card" style="left:213px;width:305px">
    <div class="info-icon"><svg width="15" height="15" viewBox="0 0 24 24" fill="none" stroke="#0054aa" stroke-width="1.8" stroke-linecap="round" stroke-linejoin="round"><path d="M11 21H5a2 2 0 0 1-2-2V6a2 2 0 0 1 2-2h14a2 2 0 0 1 2 2v5"/><path d="M16 2v4M8 2v4M3 10h18"/><circle cx="17" cy="17" r="4.5"/><path d="M17 15v2l1.3 1"/></svg></div>
    <div class="info-title">Business Hours</div>
    <div class="info-value">Monday – Friday: 7:00 AM – 5:00 PM</div>
  </div>
  <div class="abs info-card" style="left:530px;width:232px">
    <div class="info-icon"><svg width="15" height="15" viewBox="0 0 24 24" fill="none" stroke="#0054aa" stroke-width="1.8" stroke-linecap="round" stroke-linejoin="round"><rect x="3" y="5" width="18" height="14" rx="2"/><path d="M3 7l9 6 9-6"/></svg></div>
    <div class="info-title">Email Address:</div>
    <div class="info-value">info@brightlinecoatings.com</div>
  </div>

  <form>
    <label class="abs label" style="left:53px;top:401px">Full Name<i>*</i></label>
    <div class="abs field" style="left:45px;top:422px;width:352px">ex. Jordan Blake</div>
    <label class="abs label" style="left:417px;top:401px">Email Address<i>*</i></label>
    <div class="abs field" style="left:409px;top:422px;width:353px">ex. jordan@example.com</div>

    <label class="abs label" style="left:53px;top:487px">Phone Number<i>*</i></label>
    <div class="abs field" style="left:45px;top:509px;width:352px">ex. +1 (234) 567 890</div>
    <label class="abs label" style="left:417px;top:487px">Service Required<i>*</i></label>
    <div class="abs field" style="left:409px;top:509px;width:353px">Select<svg width="10" height="7" viewBox="0 0 10 7" fill="none" stroke="#2a2d31" stroke-width="1.4" stroke-linecap="round" stroke-linejoin="round"><path d="M1 1.5l4 4 4-4"/></svg></div>

    <label class="abs label" style="left:53px;top:574px">Project Location<i>*</i></label>
    <div class="abs field" style="left:45px;top:596px;width:717px">Select<svg width="10" height="7" viewBox="0 0 10 7" fill="none" stroke="#2a2d31" stroke-width="1.4" stroke-linecap="round" stroke-linejoin="round"><path d="M1 1.5l4 4 4-4"/></svg></div>

    <label class="abs label" style="left:53px;top:661px">Message<i>*</i></label>
    <div class="abs field area" style="left:45px;top:683px;width:717px">Write</div>

    <div class="abs cta">Request My Free Quote</div>
  </form>
</main>

<footer class="abs footer">
  <div class="footer-brand"><span class="mark"></span>Brightline Coatings Co</div>
  <p class="footer-about">Family-owned fabrication of aluminium and stainless steel handrails, glass.</p>
  <div class="footer-col" style="left:289px">
    <h3>SERVICES</h3>
    <ul><li>Glass Balustrades</li><li>Pool Fencing</li><li>Handrails</li><li>Electric Gates</li><li>Slat Screens</li></ul>
  </div>
  <div class="footer-col" style="left:420px">
    <h3>COMPANY</h3>
    <ul><li>About Us</li><li>Our Projects</li><li>Request a Quote</li><li>Service Areas</li></ul>
  </div>
  <div class="footer-col" style="left:550px">
    <h3>CONTACT</h3>
    <ul><li>0700 000 000</li><li>hello@brightlinecoatings.com.au</li><li>Mon–Fri: 7am – 4pm</li><li>Sat: By appointment</li></ul>
  </div>
  <p class="copyright">© 2026 Brightline Coatings Co. All rights reserved - Designed &amp; Developed by Northpoint Studio</p>
</footer>

</body>
</html>
```